New Webpage for High Class Expert Witness Services Company

We are looking for a minimalist design for a webpage that just has our logo and an entry form offer to connect with one of our Liaisons.
The entry form should just ask for Name, Email, Contact Info and Description of Project.

Company Name is: The Marlowe Crest Advisory Services

Number of Pages Required

1 page

```html
<!DOCTYPE html>
<html lang="en">
<head>
<meta charset="UTF-8">
<title>The Marlowe Crest Advisory Services</title>
<link href="https://fonts.googleapis.com/css2?family=Montserrat:wght@400;500;600&display=swap" rel="stylesheet">
<style>
:root{
  --bg-header:#141414;
  --bg-dark:#050505;
  --bg-about:#1a1a1a;
  --bg-footer:#0a0a0a;
  --field:#333333;
  --field-border:#5a5a5a;
  --text:#ffffff;
  --muted:#d6d6d6;
  --soft-grey:#a8a8a8;
  --btn-light:#f2f2f2;
  --btn-grey:#b9b9bd;
}
*{margin:0;padding:0;box-sizing:border-box}
html,body{width:773px;height:1200px;overflow:hidden;background:var(--bg-dark)}
body{font-family:'Montserrat',sans-serif;color:var(--text);position:relative}
.site-header{position:absolute;top:0;left:0;width:773px;height:55px;background:var(--bg-header);display:flex;align-items:center;justify-content:center}
.brand-name{font-size:12px;font-weight:600;letter-spacing:.6px;color:#e4e4e4;text-transform:uppercase}
.hero{position:absolute;top:55px;left:0;width:773px;height:331px;background:radial-gradient(ellipse at 30% 60%,#3a4a44 0%,#24312d 45%,#111816 100%);}
.hero-title{position:absolute;top:92px;width:100%;text-align:center;font-size:31px;font-weight:500;line-height:36px}
.btn{display:flex;align-items:center;justify-content:center;border-radius:14px;color:#111;font-family:inherit;font-weight:500}
.hero .btn{position:absolute;left:312px;top:190px;width:149px;height:25px;background:#fff;font-size:9.5px}
.contact{position:absolute;top:386px;left:0;width:773px;height:422px;background:linear-gradient(90deg,#0d0d0d,#000)}
.section-title{font-size:25px;font-weight:500;color:#d4d4d4}
.contact .section-title{position:absolute;top:52px;width:100%;text-align:center}
.contact-intro{position:absolute;top:98px;width:100%;text-align:center;font-size:9.5px;line-height:16px;color:var(--muted);font-weight:400}
.field{position:absolute;background:var(--field);border:1px solid var(--field-border);border-radius:4px;font-size:9.5px;color:#e8e8e8;padding:0 8px;display:flex;align-items:center;justify-content:space-between}
.field svg{width:10px;height:10px;fill:#fff}
.field.textarea{align-items:flex-start;padding-top:10px}
.contact .btn{position:absolute;left:346px;top:341px;width:81px;height:24px;background:linear-gradient(90deg,var(--btn-light),var(--btn-grey));font-size:9.5px}
.about{position:absolute;top:808px;left:0;width:773px;height:354px;background:var(--bg-about)}
.about .section-title{position:absolute;left:72px;top:50px;color:#fff}
.about .section-title span{color:var(--soft-grey)}
.about-lead{position:absolute;left:72px;top:98px;width:353px;font-size:11px;line-height:16.5px;font-weight:500}
.about-body{position:absolute;left:72px;top:139px;width:353px;font-size:9.3px;line-height:15px;color:#e2e2e2;text-align:justify}
.about-body p+p{margin-top:5px}
.about .btn{position:absolute;left:72px;top:274px;width:82px;height:25px;background:linear-gradient(90deg,var(--btn-light),var(--btn-grey));font-size:9.5px}
.brand-mark{position:absolute;left:510px;top:90px;width:180px;height:180px;border-radius:50%;background:#8c8c8e}
.site-footer{position:absolute;top:1162px;left:0;width:773px;height:38px;background:var(--bg-footer);display:flex;align-items:center;justify-content:center;font-size:8.5px;color:#e6e6e6}
</style>
</head>
<body>
<header class="site-header"><span class="brand-name">The Marlowe Crest Advisory Services</span></header>

<section class="hero" role="img" aria-label="Stethoscope resting on camouflage uniform fabric">
  <h1 class="hero-title">Strategic Expert Witness &amp;<br>Defense Consulting</h1>
  <a class="btn">Request a Consultation</a>
</section>

<section class="contact">
  <h2 class="section-title">Connect With Defense Liaison</h2>
  <p class="contact-intro">Lorem ipsum dolor sit amet, consectetur adipiscing elit, sed do<br>incididunt ut labore et dolore magna aliqua. Quis ipsum suspendisse ultrices gravida.</p>
  <div class="field" style="left:72px;top:156px;width:307px;height:31px">First Name
    <svg viewBox="0 0 16 16"><circle cx="8" cy="8" r="8"/><circle cx="8" cy="6" r="2.6" fill="#333"/><path d="M3.5 13a5 4 0 0 1 9 0z" fill="#333"/></svg></div>
  <div class="field" style="left:393px;top:156px;width:308px;height:31px">Last Name
    <svg viewBox="0 0 16 16"><circle cx="8" cy="8" r="8"/><circle cx="8" cy="6" r="2.6" fill="#333"/><path d="M3.5 13a5 4 0 0 1 9 0z" fill="#333"/></svg></div>
  <div class="field" style="left:72px;top:200px;width:307px;height:31px">Email Address
    <svg viewBox="0 0 16 16"><rect x="0" y="3" width="16" height="11" rx="1.5"/><path d="M0 4l8 5 8-5" stroke="#333" stroke-width="1.4" fill="none"/></svg></div>
  <div class="field" style="left:393px;top:200px;width:308px;height:31px">Phone Number
    <svg viewBox="0 0 16 16"><path d="M15 11.5l-3.3-1.4-1.7 2A10 10 0 0 1 4 6l2-1.7L4.5 1 1 1.7C1 9 7 15 14.3 15z"/></svg></div>
  <div class="field textarea" style="left:72px;top:244px;width:629px;height:72px">Description of Project
    <svg viewBox="0 0 18 16"><ellipse cx="7" cy="6" rx="7" ry="5"/><ellipse cx="12" cy="10" rx="6" ry="4.5"/></svg></div>
  <a class="btn">Submit</a>
</section>

<section class="about">
  <h2 class="section-title">About Marlowe <span>Crest</span></h2>
  <p class="about-lead">Lorem ipsum dolor sit amet, consectetur adipiscing elit, sed do eiusmod tempor incididunt ut labore</p>
  <div class="about-body">
    <p>Sed ut perspiciatis unde omnis iste natus error sit voluptatem accusantium doloremque laudantium, totam rem aperiam, eaque ipsa quae ab illo inventore veritatis et quasi architecto beatae vitae dicta sunt explicabo. Nemo enim ipsam voluptatem quia voluptas.</p>
    <p>Sit aspernatur aut odit aut fugit, sed quia consequuntur magni dolores eos qui ratione voluptatem sequi nesciunt. Neque porro quisquam est, qui dolorem ipsum quia dolor sit amet, consectetur, adipisci velit, sed quia non numquam eius modi tempora incidunt ut labore et dolore</p>
  </div>
  <a class="btn">Read More</a>
  <div class="brand-mark" aria-hidden="true"></div>
</section>

<footer class="site-footer">Copyright © 2026 Marlowe Crest. All rights reserved.</footer>
</body>
</html>
```